Children’s entertainer/balloon artist Website Home Page and custom landing page

I need a home page design for the home page of a children and family entertainer/balloon twister’s website. I also need a custom landing page for family theatre shows performed by the same entertainer.
It will be a Wordpress website and I need the final artwork in a layer Photoshop file with all the layers clearly named and labeled.

Target Market(s)

The site visitors are mainly mums, aged between early 20’s and late 30’s. Other visitors will included companies for Christmas functions, and event organisers for corporate functions.

Industry/Entity Type

Entertainment

Number of Pages Required

2 page

Font styles to use
Sans Serif

Colors
34a6d7
f37122

Requirements
Must have
• Layout
• I have included a wireframe for the home page layout and the custom landing page for your reference. This is a guide only and I welcome your interpretation with the rough layout provided.
• This website needs to look good on all devices as it will be fully responsive.
• It needs to include a footer area on the page, that has social media and a call to action area included.
• Colours
• The main colours for the site is:
• orange (call to action colour)
• ff6800
• blue/turquoise
• 42abc3
• Pictures
• I have included images of the entertainer/balloon artist for you to use/take inspiration from.
• These images will be included on the website. I want to show lots of people having fun.
• I would like to have elements of the logo used in isolation across the website
• i.e. the octopus figure to be included in the footer or the bird element to be included in the testimonial slider etc.
• Elements to include
• Note: use the images of the entertainer in the boxes on the home page (balloon shows, balloon twisting, balloon workshops, theatre shows (the three little balloon pigs on his head)
Nice to have
Should not have
• Element to avoid
• Stock imagery of balloon sculptures - use images provided.

```html
<!DOCTYPE html>
<html lang="en">
<head>
<meta charset="utf-8">
<title>Benny Bounce – Children's Entertainer</title>
<link href="https://fonts.googleapis.com/css2?family=Lobster&family=Open+Sans:ital,wght@0,400;0,600;1,400&display=swap" rel="stylesheet">
<style>
:root{
  --sky:#34a6d7;
  --sky-light:#7fd0f2;
  --orange:#f37122;
  --orange-dark:#e2611a;
  --navy:#2e3a8c;
  --hero-mid:#4a78c8;
  --text:#777;
  --heading:#555;
  --panel:#f2f2f2;
  --rule:#dcdcdc;
  --white:#fff;
  --quote:#2c3f9a;
}
*{box-sizing:border-box;margin:0;padding:0}
html,body{width:713px;height:1200px;overflow:hidden}
body{position:relative;background:var(--white);font-family:"Open Sans",Arial,sans-serif;color:var(--text)}
a{text-decoration:none}
.abs{position:absolute}

/* Header */
.site-header{position:absolute;left:0;top:0;width:713px;height:174px;background:var(--orange)}
.site-header .sky{position:absolute;left:0;top:0}
.brand{position:absolute;left:0;top:50px;width:713px;text-align:center;font-family:"Lobster",cursive;font-size:28px;color:var(--orange)}
.brand-mark{display:block;margin:0 auto 6px;width:18px;height:18px;border-radius:50%;background:var(--orange)}
.main-nav{position:absolute;left:0;top:146px;width:713px;display:flex;justify-content:center;gap:40px}
.main-nav a{font-family:"Lobster",cursive;font-size:13px;color:var(--white)}

/* Hero */
.hero{position:absolute;left:0;top:174px;width:713px;height:272px;background:radial-gradient(ellipse at 28% 40%,#5b8fd8 0%,#4266b8 40%,var(--navy) 100%)}
.hero-photo{position:absolute;left:128px;top:0;width:196px;height:272px;border-radius:0;background:linear-gradient(160deg,#3f4f7a 0%,#5a9a5a 18%,#e0b840 36%,#f08a3a 52%,#c9a0b8 68%,#9eb6dc 84%,#6e8fcf 100%)}
.hero-balloons{position:absolute;left:602px;top:140px;width:90px;height:92px;border-radius:46px 46px 40px 40px;background:linear-gradient(135deg,#7f8bd0 0%,#c56a9b 35%,#d0a86a 60%,#6aa07a 80%,#5a7ad0 100%);opacity:.85}
.hero-title{position:absolute;left:374px;top:92px;font-family:"Lobster",cursive;font-size:26px;font-weight:400;color:var(--white)}
.hero-title span{color:var(--orange)}
.hero-text{position:absolute;left:377px;top:133px;width:190px;font-family:"Lobster",cursive;font-size:11px;line-height:13.5px;color:var(--white)}
.btn{display:inline-block;font-family:"Lobster",cursive;color:var(--white);text-align:center;border-radius:13px}
.hero .btn{position:absolute;left:377px;top:185px;width:77px;height:25px;line-height:25px;font-size:11px;background:var(--orange)}

/* Main column */
.section-title{font-family:"Lobster",cursive;font-size:19px;color:var(--heading);font-weight:400}
.theatre-title{left:96px;top:462px}
.theatre-lead{left:96px;top:490px;font-family:"Lobster",cursive;font-size:10px;color:var(--orange)}
.theatre-body{left:96px;top:509px;width:384px;font-size:6.4px;line-height:11px}
.theatre-btn{position:absolute;left:96px;top:562px;width:58px;height:21px;line-height:21px;font-size:9.5px;background:var(--sky)}
.divider{left:96px;top:600px;width:384px;height:1px;background:var(--rule)}
.video-title{left:96px;top:614px}
.video{left:96px;top:646px;width:384px;height:198px;background:linear-gradient(120deg,#2d3f9c 0%,#3a5cc0 22%,#c9987a 42%,#e8c040 58%,#8ab050 72%,#e08aa0 86%,#3a58b8 100%)}
.video svg{position:absolute;left:169px;top:76px}

.testimonial{left:96px;top:864px;width:384px;height:108px;background:var(--panel)}
.testimonial .section-title{position:absolute;left:16px;top:7px}
.testimonial .arrows{position:absolute;right:14px;top:15px}
.testimonial blockquote{position:absolute;left:16px;top:38px;width:354px;font-size:6.2px;line-height:10.5px;font-style:italic;color:var(--quote)}
.testimonial cite{position:absolute;left:19px;top:88px;font-size:7.5px;font-weight:600;font-style:normal;color:var(--orange)}

/* Sidebar */
.widget{position:absolute;left:494px;width:123px}
.widget-head{height:27px;line-height:27px;padding-left:9px;font-family:"Lobster",cursive;font-size:12.5px;color:var(--white)}
.events{top:467px;height:187px;border:1px solid #e3e3e3;border-top:0}
.events .widget-head{background:var(--orange);margin:0 -1px}
.event{display:flex;gap:7px;padding:7px 8px;height:53px;border-bottom:1px solid #e6e6e6}
.event:last-child{border-bottom:0}
.event-thumb{width:40px;height:32px;flex:none}
.event-text{font-size:5.2px;line-height:9px;color:#888}
.event-text time{display:block;font-family:"Lobster",cursive;font-size:5px;color:var(--orange)}
.newsletter{top:662px;height:140px;background:var(--sky)}
.newsletter p{padding:4px 9px 0;font-size:5.4px;line-height:9px;color:var(--white)}
.field{margin:6px 10px 0;height:19px;background:var(--white);font-size:5.5px;line-height:19px;padding-left:4px;color:#666}
.newsletter .btn{margin:9px 0 0 9px;width:84px;height:20px;line-height:18px;font-size:9.5px;border:1.5px solid var(--white);border-radius:11px}
.tweets{top:812px;height:160px;border:1px solid #dcdcdc;background:#fafafa}
.tweets .widget-head{color:var(--heading);font-size:12px;display:flex;justify-content:space-between;align-items:center;padding-right:6px;border-bottom:1px solid #e6e6e6}
.follow{font-family:"Open Sans",Arial,sans-serif;font-size:5px;color:#333;border:1px solid #ccc;border-radius:2px;padding:0 5px;height:11px;line-height:10px;background:#f5f5f5}
.tweet{display:flex;gap:6px;padding:6px 10px 6px 6px;height:61px;border-bottom:1px solid #e6e6e6;background:var(--white);margin-right:8px}
.avatar{width:20px;height:20px;background:var(--sky);flex:none}
.tweet-body{font-size:5.2px;line-height:7.5px;color:#777;width:80px}
.tweet-body b{font-weight:600;color:#444;display:flex;justify-content:space-between}
.tweet-body a{color:var(--sky);font-style:italic}
.tweet-to{position:absolute;left:4px;bottom:3px;width:114px;height:12px;line-height:12px;text-align:center;background:var(--white);font-size:5.2px;color:#555}
.scrollbar{position:absolute;right:1px;top:30px;width:6px;height:110px;background:#eee}

/* Connect */
.connect-title{left:0;top:998px;width:713px;text-align:center;font-family:"Lobster",cursive;font-size:13px;font-weight:400;color:var(--heading)}
.connect-text{left:250px;top:1024px;width:213px;text-align:center;font-size:6.3px;line-height:11px;color:#888}
.mail-icon{left:184px;top:1054px;width:34px;height:34px;border-radius:50%;background:var(--orange)}
.mail-icon svg{position:absolute;left:9px;top:11px}
.email-input{left:224px;top:1060px;width:247px;height:26px;border:1px solid var(--orange);border-radius:3px;font-size:6.2px;line-height:24px;padding-left:10px;color:#777}
.go{left:474px;top:1060px;width:28px;height:26px;line-height:26px;background:var(--orange);border-radius:2px;font-size:12px}

/* Footer */
.site-footer{position:absolute;left:0;top:1114px;width:713px;height:86px;background:radial-gradient(ellipse at 50% 0%,#f6874a 0%,var(--orange) 45%,var(--orange-dark) 100%);color:var(--white);text-align:center}
.social{position:absolute;left:0;top:11px;width:713px;display:flex;justify-content:center;gap:4px}
.social svg{display:block}
.footer-nav{position:absolute;top:39px;width:713px;font-size:6.3px}
.footer-contact{position:absolute;top:52px;width:713px;font-size:6.3px}
.copyright{position:absolute;top:65px;width:713px;font-size:5.2px}
</style>
</head>
<body>

<header class="site-header">
  <svg class="sky" width="713" height="140" viewBox="0 0 713 140" aria-hidden="true">
    <defs>
      <radialGradient id="skyGlow" cx="50%" cy="90%" r="70%">
        <stop offset="0" stop-color="#7fd0f2"/>
        <stop offset="1" stop-color="#34a6d7"/>
      </radialGradient>
    </defs>
    <path d="M0 0H713V106Q356 145 0 106Z" fill="url(#skyGlow)"/>
  </svg>
  <div class="brand"><span class="brand-mark"></span>Benny Bounce</div>
  <nav class="main-nav">
    <a href="#">Home</a><a href="#">Balloon Shows</a><a href="#">Balloon Twisting</a><a href="#">Theatre</a><a href="#">Reviews</a><a href="#">Contact</a>
  </nav>
</header>

<section class="hero">
  <div class="hero-photo" role="img" aria-label="Entertainer holding an armful of colourful balloon sculptures"></div>
  <h1 class="hero-title">Benny <span>Marlowe</span></h1>
  <p class="hero-text">Sed ut perspiciatis unde omnis iste<br>natu s error sit voluptatem accusantum<br>doloremque lauda.</p>
  <a class="btn" href="#">Read More</a>
  <div class="hero-balloons" role="img" aria-label="Bunch of coloured party balloons"></div>
</section>

<h2 class="abs section-title theatre-title">Theatre Performance</h2>
<p class="abs theatre-lead">Sed ut perspiciatis unde omnis iste natus error sit voluptatem accu santium doloremque laudan</p>
<p class="abs theatre-body">Sed ut perspiciatis unde omnis iste natus error sit voluptatem accusantium doloremque laudantium, totam rem aperiam, eaque ipsa quae ab illo inventore veritatis.Nemo enim ipsam voluptatem quia voluptas sit aspernatur aut odit aut fugit,d ut perspiciatis unde omnis iste natus error sit voluptatem accusantium doloremque laudantium, totam rem aperiamSed ut perspiciatis unde omnis iste natus error sit voluptatem accusantium doloremque laudantium, totam rem aperiam, eaque</p>
<a class="btn theatre-btn" href="#">Read More</a>
<div class="abs divider"></div>

<h2 class="abs section-title video-title">Our Video</h2>
<div class="abs video" role="img" aria-label="Video still of the entertainer surrounded by long twisting balloons">
  <svg width="46" height="46" viewBox="0 0 46 46" aria-hidden="true">
    <circle cx="23" cy="23" r="21" fill="rgba(0,0,0,.2)" stroke="#fff" stroke-width="2.4"/>
    <path d="M18 14L32 23L18 32Z" fill="#fff"/>
  </svg>
</div>

<section class="abs testimonial">
  <h2 class="section-title">Testimonial</h2>
  <svg class="arrows" width="22" height="10" viewBox="0 0 22 10" aria-hidden="true">
    <circle cx="5" cy="5" r="4.3" fill="none" stroke="#f37122" stroke-width="1.2"/><path d="M6.3 3L4 5L6.3 7" fill="none" stroke="#f37122" stroke-width="1.2"/>
    <circle cx="17" cy="5" r="4.3" fill="none" stroke="#f37122" stroke-width="1.2"/><path d="M15.7 3L18 5L15.7 7" fill="none" stroke="#f37122" stroke-width="1.2"/>
  </svg>
  <blockquote>“ Sed ut perspiciatis unde omnis iste natus error sit voluptatem accusantium doloremque laudantium, totam rem aperiam, eaq ue ipsa quae ab illo inventore veritatis et quasi architecto beatae vitae dicta sunt explicabo. Nemo enim ipsam voluptatem quia voluptas sit aspernatur aut odit aut fugit, sed quia consequuntur magni dolores eos qui ratione voluptatem sequi nesciunt. Neque porro quisquam est, qui dolorem ipsum quia dolor sit amet, consectetur, adipisc ”</blockquote>
  <cite>Clara Hood, city Name</cite>
</section>

<aside class="widget events">
  <div class="widget-head">Upcoming Events</div>
  <div class="event"><div class="event-thumb" role="img" aria-label="Entertainer on stage" style="background:linear-gradient(135deg,#3a6fc0,#9fb8e0)"></div><div class="event-text">Lorem ipsum dom etcons ectetur adipis cing elitseddoei<time>Oct 28 2015</time></div></div>
  <div class="event"><div class="event-thumb" role="img" aria-label="Entertainer with balloon sculptures" style="background:linear-gradient(135deg,#4a5fb8,#e0b040)"></div><div class="event-text">Lorem ipsum dom etcons ectetur adipis cing elitseddoei<time>Oct 28 2015</time></div></div>
  <div class="event"><div class="event-thumb" role="img" aria-label="Three balloon pigs for the theatre show" style="background:linear-gradient(135deg,#f0a0b8,#c9b8c0)"></div><div class="event-text">Lorem ipsum dom etcons ectetur<time>Oct 28 2015</time></div></div>
</aside>

<aside class="widget newsletter">
  <div class="widget-head">Newsletter Signup</div>
  <p>Lorem ipsum dom etcons ecteturpis cing elitseddom etcons ectei.</p>
  <div class="field">Name:</div>
  <div class="field">Email:</div>
  <a class="btn" href="#">Subscribe Now</a>
</aside>

<aside class="widget tweets">
  <div class="widget-head">Tweets <span class="follow">Follow</span></div>
  <div class="tweet"><div class="avatar"></div><div class="tweet-body"><b>Benny Marlowe <span>6 Nov</span></b>@B_Bounce<br>Lorem ipsum dometcons tetur adipiscing <a href="#">@Benny Marlowe</a></div></div>
  <div class="tweet"><div class="avatar"></div><div class="tweet-body"><b>Benny Marlowe <span>6 Nov</span></b>@B_Bounce<br>Lorem ipsum dometcons tetur adipiscing <a href="#">@Benny Marlowe</a></div></div>
  <div class="scrollbar"></div>
  <div class="tweet-to">Tweet to @ B-Marlowe</div>
</aside>

<h2 class="abs connect-title">Coonect With Benny Marlowe</h2>
<p class="abs connect-text">Sed ut perspiciatis unde omnis iste natus error sit voluptatem accusan-tium doloremque laudantium, totam rem aperiam, eaque ips</p>
<div class="abs mail-icon">
  <svg width="16" height="12" viewBox="0 0 16 12" aria-hidden="true"><rect x="0.7" y="0.7" width="14.6" height="10.6" rx="1" fill="#fff"/><path d="M1 1L8 7L15 1" fill="none" stroke="#f37122" stroke-width="1.2"/></svg>
</div>
<div class="abs email-input">Enter Email Addres:</div>
<a class="abs btn go" href="#">Go</a>

<footer class="site-footer">
  <div class="social" aria-label="Social links">
    <svg width="18" height="18" viewBox="0 0 18 18" aria-hidden="true"><circle cx="9" cy="9" r="8.2" fill="rgba(255,255,255,.12)" stroke="#fff" stroke-width="1.3"/><circle cx="9" cy="9" r="3" fill="#fff"/></svg>
    <svg width="18" height="18" viewBox="0 0 18 18" aria-hidden="true"><circle cx="9" cy="9" r="8.2" fill="rgba(255,255,255,.12)" stroke="#fff" stroke-width="1.3"/><circle cx="9" cy="9" r="3" fill="#fff"/></svg>
    <svg width="18" height="18" viewBox="0 0 18 18" aria-hidden="true"><circle cx="9" cy="9" r="8.2" fill="rgba(255,255,255,.12)" stroke="#fff" stroke-width="1.3"/><circle cx="9" cy="9" r="3" fill="#fff"/></svg>
    <svg width="18" height="18" viewBox="0 0 18 18" aria-hidden="true"><circle cx="9" cy="9" r="8.2" fill="rgba(255,255,255,.12)" stroke="#fff" stroke-width="1.3"/><circle cx="9" cy="9" r="3" fill="#fff"/></svg>
  </div>
  <div class="footer-nav">Home &nbsp;| &nbsp;Balloon Shows &nbsp;| &nbsp;Balloon Twisting &nbsp;| &nbsp;Theatre &nbsp;| &nbsp;Reviews &nbsp;| &nbsp;Contact</div>
  <div class="footer-contact">Call Us: 0044 -555-210 &nbsp;Location: lorem ispsum dolor site dummy addre . Email:hello@example.com</div>
  <div class="copyright">Copyright 2015 &nbsp;All Rights Reserved.</div>
</footer>

</body>
</html>
```